Business Card Design for company

We want new business cards. We'd like something different-- yet still highly professional. Our tagline is Providing leadership, delivering success. Stock photos are ok, as long as they are relevant and look upscale.

Target Market(s)

Architecture/Business Management Consulting/Engineering Consulting

Contact Information for Business Card

dark gray background with pops of blue might be good, but you tell me. You're the designers. Rounded corners might be nice, but again, you tell me.

Font styles to use
Serif
Sans Serif

Colors
3276b5
5c5c5c
9d9d9d
fbfbfb

Requirements
Nice to have
• Something different, but still very professional.

```html
<!DOCTYPE html>
<html lang="en">
<head>
<meta charset="utf-8">
<title>Halvern Group – Business Card</title>
<link rel="stylesheet" href="https://fonts.googleapis.com/css2?family=Open+Sans:wght@400;600&display=swap">
<style>
  :root {
    --blue: #3276b5;
    --dark-gray: #5c5c5c;
    --mid-gray: #9d9d9d;
    --off-white: #fbfbfb;
    --card-black: #0b0b0b;
    --backdrop: #e6e4e0;
    --wordmark: #6e6e6e;
  }
  * { margin: 0; padding: 0; box-sizing: border-box; }
  html, body { width: 1200px; height: 1023px; overflow: hidden; }
  body {
    background: var(--backdrop);
    font-family: "Open Sans", Arial, sans-serif;
    position: relative;
  }
  .card {
    position: absolute;
    left: 250px;
    width: 700px;
    height: 400px;
    background: radial-gradient(ellipse at 40% 40%, #1c1c1c 0%, var(--card-black) 70%);
    overflow: hidden;
    box-shadow: 0 6px 18px rgba(0,0,0,0.25);
  }
  .card--front { top: 70px; }
  .card--back { top: 553px; }

  /* striped bands */
  .stripe-band { position: absolute; display: flex; }
  .stripe-band--side { left: 0; top: 0; width: 26px; height: 400px; flex-direction: column; }
  .stripe-band--top { left: 0; top: 0; width: 700px; height: 26px; flex-direction: row; }
  .stripe-band span { flex: 1; }
  .s-blue { background: var(--blue); }
  .s-dark { background: var(--dark-gray); }
  .s-mid { background: var(--mid-gray); }
  .s-light { background: var(--off-white); }

  /* wordmark */
  .wordmark {
    position: absolute;
    display: flex;
    align-items: center;
    gap: 16px;
  }
  .card--front .wordmark { left: 62px; bottom: 58px; }
  .wordmark__square { width: 22px; height: 22px; background: var(--blue); }
  .wordmark__name {
    font-size: 50px;
    font-weight: 600;
    color: var(--wordmark);
    letter-spacing: 1px;
    line-height: 1;
  }

  /* person */
  .person {
    position: absolute;
    right: 96px;
    top: 46px;
    text-align: right;
  }
  .person__name { font-size: 27px; font-weight: 600; color: var(--off-white); line-height: 1.1; }
  .person__role { font-size: 16px; color: var(--blue); }

  /* contact list */
  .contact-list {
    position: absolute;
    right: 0;
    top: 112px;
    list-style: none;
  }
  .contact-item {
    display: flex;
    justify-content: flex-end;
    align-items: flex-start;
  }
  .contact-item__text {
    font-size: 15.5px;
    color: var(--off-white);
    text-align: right;
    padding: 8px 16px 0 0;
    line-height: 1.3;
  }
  .contact-item__icon {
    width: 38px;
    height: 38px;
    display: flex;
    align-items: center;
    justify-content: center;
    flex-shrink: 0;
  }
  .contact-item__icon svg { width: 18px; height: 18px; }

  /* back */
  .card--back .wordmark {
    left: 50%;
    top: 50%;
    transform: translate(-50%, -40%);
  }
  .tagline {
    position: absolute;
    left: 0; right: 0;
    bottom: 80px;
    text-align: center;
    font-size: 15px;
    color: var(--mid-gray);
    letter-spacing: 2px;
  }
</style>
</head>
<body>

<section class="card card--front" aria-label="Business card front">
  <div class="stripe-band stripe-band--side">
    <span class="s-blue"></span><span class="s-dark"></span><span class="s-mid"></span><span class="s-light"></span>
    <span class="s-blue"></span><span class="s-dark"></span><span class="s-mid"></span><span class="s-light"></span>
  </div>

  <div class="wordmark">
    <span class="wordmark__square"></span>
    <span class="wordmark__name">Halvern Group</span>
  </div>

  <div class="person">
    <p class="person__name">Daniel Ross</p>
    <p class="person__role">Owner</p>
  </div>

  <ul class="contact-list">
    <li class="contact-item">
      <span class="contact-item__text">+0000-0000-0000</span>
      <span class="contact-item__icon s-blue">
        <svg viewBox="0 0 24 24"><path fill="#111" d="M6.6 10.8a15 15 0 0 0 6.6 6.6l2.2-2.2c.3-.3.7-.4 1-.2 1.1.4 2.3.6 3.6.6.6 0 1 .4 1 1V20c0 .6-.4 1-1 1A17 17 0 0 1 3 4c0-.6.4-1 1-1h3.5c.6 0 1 .4 1 1 0 1.3.2 2.5.6 3.6.1.3 0 .7-.2 1z"/></svg>
      </span>
    </li>
    <li class="contact-item">
      <span class="contact-item__text">info@yourdomain.com</span>
      <span class="contact-item__icon s-dark">
        <svg viewBox="0 0 24 24"><rect x="3" y="5" width="18" height="14" fill="none" stroke="#111" stroke-width="2"/><path d="M3 5l9 8 9-8" fill="none" stroke="#111" stroke-width="2"/></svg>
      </span>
    </li>
    <li class="contact-item">
      <span class="contact-item__text">www.yourdomain.com</span>
      <span class="contact-item__icon s-mid">
        <svg viewBox="0 0 24 24"><circle cx="12" cy="12" r="9" fill="none" stroke="#111" stroke-width="2"/><path d="M3 12h18M12 3c3 3 3 15 0 18M12 3c-3 3-3 15 0 18" fill="none" stroke="#111" stroke-width="1.6"/></svg>
      </span>
    </li>
    <li class="contact-item">
      <span class="contact-item__text">Suite 210, 48 Harrow Lane,<br>Bristol</span>
      <span class="contact-item__icon s-light">
        <svg viewBox="0 0 24 24"><path fill="#111" d="M12 2a7 7 0 0 0-7 7c0 5 7 13 7 13s7-8 7-13a7 7 0 0 0-7-7zm0 9.5A2.5 2.5 0 1 1 12 6.5a2.5 2.5 0 0 1 0 5z"/></svg>
      </span>
    </li>
  </ul>
</section>

<section class="card card--back" aria-label="Business card back">
  <div class="stripe-band stripe-band--top">
    <span class="s-light"></span><span class="s-mid"></span><span class="s-dark"></span><span class="s-blue"></span>
    <span class="s-light"></span><span class="s-mid"></span><span class="s-dark"></span><span class="s-blue"></span>
  </div>
  <div class="wordmark">
    <span class="wordmark__square"></span>
    <span class="wordmark__name">Halvern Group</span>
  </div>
</section>

</body>
</html>
```